Dynamic Business Card for Sports Supplements Company

Hi! I'm looking for an awesome business card to match my existing sports supplement company. I have uploaded my current company logo and screenshot of the front page of my website.

I would like to have something dynamic and interesting and utilize the colors in the website - the reds and purples

The business card should be double sided and focus on a unique eye-catching design on the back and include all the relevant company info.

Most importantly, it should say somewhere: "Sign up on our website for a coupon code."

Target Market(s)

Mostly for women gym goers but it shouldn't be too feminine. It should be in keeping with the website design. It should flow and clearly be connected to it

Industry/Entity Type

Business

Contact Information for Business Card

Lorraine K. Vestal
CEO
LVestal@Quorvanexco.com
www.quorvanexco.com
555.417.3820
P.O. Box 47315
Halvers, Northmere 00000

Sign up on our website for a coupon code

Font styles to use
Serif
Sans Serif
Other font styles liked:
• Novecento font family and "Quorvanex" is in AR Destine font

Requirements
Must have
• One side should be a bold Quorvanex logo design. Even just the symbol itself may be o.k. (see attached file)

```html
<!DOCTYPE html>
<html lang="en">
<head>
<meta charset="utf-8">
<title>Quorvanex Business Card</title>
<link href="https://fonts.googleapis.com/css2?family=Montserrat:wght@400;500;700;800&display=swap" rel="stylesheet">
<style>
  :root {
    --backdrop: #3a3a3c;
    --indigo: #332c5e;
    --violet-stripe: #6a4c9c;
    --signal-red: #e0202a;
    --paper: #ffffff;
    --ink: #111111;
  }
  html, body {
    margin: 0;
    padding: 0;
    width: 1200px;
    height: 855px;
    overflow: hidden;
    background: var(--backdrop);
    font-family: "Montserrat", sans-serif;
  }
  .canvas {
    position: relative;
    width: 1200px;
    height: 855px;
  }
  .card {
    position: absolute;
    left: 354px;
    width: 493px;
    box-shadow: 0 6px 18px rgba(0,0,0,0.45);
    overflow: hidden;
  }
  /* Front side */
  .card-front {
    top: 137px;
    height: 281px;
    background: var(--indigo);
    color: var(--paper);
  }
  .front-brand {
    position: absolute;
    left: 0;
    right: 0;
    top: 124px;
    display: flex;
    align-items: center;
    justify-content: center;
    gap: 12px;
  }
  .front-brand .dot {
    flex: none;
    width: 26px;
    height: 26px;
    border-radius: 50%;
    border: 4px solid var(--paper);
    box-sizing: border-box;
  }
  .front-brand .name {
    font-weight: 800;
    font-size: 28px;
    letter-spacing: 1px;
  }
  .coupon-line {
    position: absolute;
    left: 0;
    right: 0;
    top: 239px;
    margin: 0;
    text-align: center;
    font-size: 12.5px;
    font-weight: 400;
    letter-spacing: 0.2px;
  }
  /* Back side */
  .card-back {
    top: 431px;
    height: 288px;
    background: var(--paper);
  }
  .diagonal {
    position: absolute;
    inset: 0;
  }
  .contact {
    position: absolute;
    left: 26px;
    top: 120px;
    color: var(--paper);
    font-size: 13px;
    line-height: 17px;
  }
  .contact .person {
    font-size: 18.5px;
    font-weight: 500;
    line-height: 22px;
  }
  .contact .role { margin-bottom: 12px; }
  .contact .address { margin-bottom: 12px; }
  .contact .line {
    display: flex;
    align-items: center;
    gap: 5px;
  }
  .contact .line svg { width: 11px; height: 11px; flex: none; }
  .brand-block {
    position: absolute;
    left: 290px;
    width: 190px;
    top: 94px;
    text-align: center;
    color: var(--ink);
  }
  .brand-block .wordmark {
    display: flex;
    align-items: center;
    justify-content: center;
    gap: 7px;
  }
  .brand-block .dot {
    flex: none;
    width: 13px;
    height: 13px;
    border-radius: 50%;
    background: var(--signal-red);
  }
  .brand-block .name {
    font-weight: 800;
    font-size: 22px;
    letter-spacing: 0.5px;
  }
  .brand-block .tagline {
    font-size: 8.5px;
    font-weight: 500;
    letter-spacing: 0.6px;
    margin-top: 2px;
  }
</style>
</head>
<body>
<div class="canvas">

  <section class="card card-front">
    <div class="front-brand">
      <span class="dot"></span>
      <span class="name">QUORVANEX</span>
    </div>
    <p class="coupon-line">Sign up on our website for a coupon code</p>
  </section>

  <section class="card card-back">
    <svg class="diagonal" viewBox="0 0 493 288" preserveAspectRatio="none" aria-hidden="true">
      <polygon points="0,0 115,0 382,288 0,288" fill="var(--indigo)"/>
      <line x1="117" y1="0" x2="389" y2="293" stroke="var(--violet-stripe)" stroke-width="3.5"/>
    </svg>

    <div class="contact">
      <div class="person">Lorraine K. Vestal</div>
      <div class="role">CEO</div>
      <div class="address">P.O. Box 47315<br>Halvers, Northmere 00000</div>
      <div class="line">
        <svg viewBox="0 0 12 12"><path d="M3 1 L5 3.5 L4 5 Q5 7 7 8 L8.5 7 L11 9 L9.5 11 Q4 10.5 1 3 Z" fill="var(--paper)"/></svg>
        <span>555.417.3820</span>
      </div>
      <div class="line">
        <svg viewBox="0 0 12 12"><rect x="0.5" y="2.5" width="11" height="7" fill="var(--paper)"/><path d="M0.5 2.5 L6 7 L11.5 2.5" fill="none" stroke="var(--indigo)" stroke-width="1"/></svg>
        <span>LVestal@Quorvanexco.com</span>
      </div>
      <div class="line">
        <svg viewBox="0 0 12 12" fill="none" stroke="var(--paper)" stroke-width="1"><circle cx="6" cy="6" r="5"/><ellipse cx="6" cy="6" rx="2.2" ry="5"/><line x1="1" y1="6" x2="11" y2="6"/></svg>
        <span>www.quorvanexco.com</span>
      </div>
    </div>

    <div class="brand-block">
      <div class="wordmark">
        <span class="dot"></span>
        <span class="name">QUORVANEX</span>
      </div>
      <div class="tagline">FUEL FOR EVERY WORKOUT</div>
    </div>
  </section>

</div>
</body>
</html>
```